Travel Agency Website - Simple General

Need a 7 page simple design that is pretty repetitive. Need to be able to load quickly that is SEO optimized. Trying to give ideas on what they can do, be personal as we are local, but at the same time come across as professional and get information easily with little burden.

- Landing Page
- Brimwell Vacations Page
- Family Trips
- Road Trips from Texas
- Other Destinations
- About Us Page
- Contact Us Page

Target Market(s)

Families

Coding

Coded - Design and coding required

Number of Pages Required

5+ page

Colors

Designer to choose colors to be used in the design.

Requirements
Must have
• Like it to flow easily with our logo. Use that for colors, etc.

```html
<!DOCTYPE html>
<html lang="en">
<head>
<meta charset="utf-8">
<title>Hum As You Roam Travel Co. – Brimwell Trips &amp; Texas Adventures</title>
<link href="https://fonts.googleapis.com/css2?family=Poppins:wght@400;500;600&family=Playfair+Display:wght@800;900&family=Pinyon+Script&display=swap" rel="stylesheet">
<style>
:root{
  --teal:#0c4a56;
  --teal-deep:#0a4350;
  --ink:#141414;
  --head-teal:#1f4d5e;
  --cream:#fbf6ee;
  --white:#ffffff;
  --rule:#d9d9d4;
}
*{box-sizing:border-box;margin:0;padding:0}
html,body{width:964px;height:1200px;overflow:hidden}
body{position:relative;font-family:"Poppins",sans-serif;color:var(--ink);
  background:radial-gradient(ellipse at 15% 30%,#e3eef0 0,transparent 45%),
             radial-gradient(ellipse at 90% 80%,#dcebee 0,transparent 40%),
             linear-gradient(180deg,#fbfaf6 0,var(--cream) 40%,#eef4f3 80%)}
.abs{position:absolute}
a{text-decoration:none;color:inherit}
.social{top:15px;width:26px;height:26px;border-radius:50%;background:var(--white);box-shadow:0 2px 6px rgba(0,0,0,.12);display:flex;align-items:center;justify-content:center}
.social.active{background:var(--teal)}
.rule{height:1px;background:var(--rule)}
.nav{top:74px;font-size:11.5px;color:#222;white-space:nowrap}
.contact-info .label{font-size:10.5px;color:var(--teal)}
.contact-info .value{font-size:11.5px;font-weight:500;margin-top:3px}
.icon-badge{width:36px;height:36px;border-radius:50%;background:var(--white);box-shadow:0 2px 8px rgba(0,0,0,.12);display:flex;align-items:center;justify-content:center}
.btn{background:var(--teal);color:var(--white);border-radius:18px;font-size:11.5px;font-weight:500;display:flex;align-items:center;justify-content:center}
.brand{left:412px;width:140px;text-align:center;font-weight:600;color:var(--teal);font-size:15px;line-height:1.15}
.brand-dot{width:10px;height:10px;border-radius:50%;background:#c9a45a;margin:0 auto 5px}
.hero-title{top:150px;left:0;width:964px;text-align:center;font-family:"Playfair Display",serif;font-weight:900;font-size:38px;letter-spacing:-.5px}
.hero-title .accent{color:var(--head-teal)}
.hero-sub{top:188px;left:0;width:964px;text-align:center;font-family:"Playfair Display",serif;font-weight:800;font-size:18.5px}
.hero-sub .script{font-family:"Pinyon Script",cursive;font-weight:400;font-size:42px;color:var(--teal);margin-left:6px}
.tile{top:277px;width:225px;height:294px;border-radius:8px}
.tile-label{top:589px;width:225px;text-align:center;font-size:13.5px;font-weight:500}
.about-title{top:676px;left:0;width:964px;text-align:center;font-family:"Playfair Display",serif;font-weight:900;font-size:38px}
.about-title span{color:var(--head-teal)}
.about-copy{left:172px;width:620px;text-align:center;font-size:10.8px;line-height:18px;color:#333}
footer{position:absolute;left:0;top:972px;width:964px;height:228px;background:var(--teal-deep);color:var(--white)}
footer .nav{color:var(--white);font-weight:500}
footer .rule{background:rgba(255,255,255,.25)}
footer .contact-info .label{color:var(--white)}
.fsocial{width:26px;height:26px;border-radius:50%;background:var(--white);display:flex;align-items:center;justify-content:center}
.copyright{top:194px;left:0;width:964px;text-align:center;font-size:10.5px}
</style>
</head>
<body>
<header>
  <a class="abs social" style="left:90px" aria-label="Share">
    <svg width="11" height="11" viewBox="0 0 24 24"><g fill="#111"><circle cx="18" cy="5" r="3"/><circle cx="6" cy="12" r="3"/><circle cx="18" cy="19" r="3"/></g><path d="M18 5L6 12l12 7" stroke="#111" stroke-width="2" fill="none"/></svg>
  </a>
  <a class="abs social active" style="left:120px" aria-label="Link">
    <svg width="11" height="11" viewBox="0 0 24 24" fill="none" stroke="#fff" stroke-width="2.5" stroke-linecap="round"><path d="M10 14a4 4 0 0 0 6 0l3-3a4 4 0 0 0-6-6l-1 1"/><path d="M14 10a4 4 0 0 0-6 0l-3 3a4 4 0 0 0 6 6l1-1"/></svg>
  </a>
  <a class="abs social" style="left:150px" aria-label="Phone">
    <svg width="11" height="11" viewBox="0 0 24 24"><path fill="#111" d="M6.6 10.8a15 15 0 0 0 6.6 6.6l2.2-2.2c.3-.3.7-.4 1-.2 1.1.4 2.3.6 3.6.6.6 0 1 .4 1 1V20c0 .6-.4 1-1 1A17 17 0 0 1 3 4c0-.6.4-1 1-1h3.5c.6 0 1 .4 1 1 0 1.2.2 2.4.6 3.6.1.3 0 .7-.2 1z"/></svg>
  </a>
  <div class="abs rule" style="top:55px;left:72px;width:332px"></div>
  <div class="abs rule" style="top:55px;left:548px;width:334px"></div>
  <nav>
    <a class="abs nav" style="left:72px">Home</a>
    <a class="abs nav" style="left:112px">Brimwell Vacations</a>
    <a class="abs nav" style="left:240px">Family Trips</a>
    <a class="abs nav" style="left:326px">About Us</a>
    <a class="abs nav" style="left:560px">Road Trips from Texas</a>
    <a class="abs nav" style="left:698px">Other Destinations</a>
    <a class="abs btn" style="left:815px;top:64px;width:100px;height:34px">Contact Us</a>
  </nav>
  <div class="abs brand" style="top:34px"><div class="brand-dot"></div>Hum As You Roam<br>Travel Co.</div>
  <div class="abs icon-badge" style="left:627px;top:9px">
    <svg width="14" height="11" viewBox="0 0 24 18"><rect width="24" height="18" rx="2" fill="var(--teal)"/><path d="M2 3l10 7 10-7" stroke="#fff" stroke-width="2" fill="none"/></svg>
  </div>
  <div class="abs contact-info" style="left:670px;top:9px"><div class="label">Email Us Today</div><div class="value">hello@humasyouroam.com</div></div>
</header>

<main>
  <h1 class="abs hero-title"><span class="accent">HUM</span> AS YOU ROAM</h1>
  <p class="abs hero-sub">MAGICAL BRIMWELL TRIPS &amp; TEXAS <span class="script">Adventures!</span></p>

  <div class="abs tile" role="img" aria-label="Photo of a turquoise coastline with waves at sunset" style="left:14px;clip-path:polygon(0 10%,100% 0,100% 100%,0 89%);background:linear-gradient(180deg,#5a6f86 0,#d9a64a 18%,#1f7e8a 30%,#0e5a68 100%)"></div>
  <div class="abs tile" role="img" aria-label="Photo of a family with swim rings by their car at the beach" style="left:251px;background:linear-gradient(180deg,#8fb4cc 0,#3b4c66 35%,#c7544a 60%,#3aa7c2 85%,#b7a68e 100%)"></div>
  <div class="abs tile" role="img" aria-label="Photo of an open desert highway at golden hour" style="left:488px;background:linear-gradient(180deg,#e7b64a 0,#f2d58a 35%,#b98a4a 50%,#6b4c32 75%,#c58a3a 100%)"></div>
  <div class="abs tile" role="img" aria-label="Photo of a surfer riding a turquoise wave" style="left:725px;clip-path:polygon(0 0,100% 10%,100% 89%,0 100%);background:linear-gradient(160deg,#1e8fa8 0,#44c1c8 40%,#bfe9ea 70%,#2aa2b4 100%)"></div>

  <h2 class="abs tile-label" style="left:14px">Brimwell Vacations</h2>
  <h2 class="abs tile-label" style="left:251px">Family Trips</h2>
  <h2 class="abs tile-label" style="left:488px">Texas Road Trips</h2>
  <h2 class="abs tile-label" style="left:725px">Other Destinations</h2>

  <h2 class="abs about-title">ABOUT <span>US</span></h2>
  <p class="abs about-copy" style="top:744px">Lorem ipsum dolor sit amet, consectetur adipiscing elit, sed do eiusmod tempor incididunt ut labore et dolore magna aliqua. Ut enim ad minim veniam, quis nostrud exercitation ullam</p>
  <p class="abs about-copy" style="top:798px">Lorem ipsum dolor sit amet, consectetur adipiscing elit, sed do eiusmod tempor incididunt ut labore et dolore magna aliqua. Ut enim ad minim veniam, quis nostrud exercitation ullamco laboris nisi ut aliquip ex ea commodo consequat. Duis aute irure dolor in reprehenderit in voluptate velit esse cillum dolore eu fugiat nulla pariatur.</p>
  <a class="abs btn" style="left:433px;top:876px;width:99px;height:33px">Learn More</a>
</main>

<footer>
  <div class="abs icon-badge" style="left:74px;top:51px;width:33px;height:33px">
    <svg width="13" height="13" viewBox="0 0 24 24"><path fill="var(--teal)" d="M6.6 10.8a15 15 0 0 0 6.6 6.6l2.2-2.2c.3-.3.7-.4 1-.2 1.1.4 2.3.6 3.6.6.6 0 1 .4 1 1V20c0 .6-.4 1-1 1A17 17 0 0 1 3 4c0-.6.4-1 1-1h3.5c.6 0 1 .4 1 1 0 1.2.2 2.4.6 3.6.1.3 0 .7-.2 1z"/></svg>
  </div>
  <div class="abs contact-info" style="left:116px;top:54px"><div class="label">Cal Us Today</div><div class="value" style="letter-spacing:1.5px">111.111.1111</div></div>
  <div class="abs brand" style="top:56px;color:var(--white)"><div class="brand-dot"></div>Hum As You Roam<br>Travel Co.</div>
  <div class="abs icon-badge" style="left:625px;top:49px">
    <svg width="14" height="11" viewBox="0 0 24 18"><rect width="24" height="18" rx="2" fill="var(--teal)"/><path d="M2 3l10 7 10-7" stroke="#fff" stroke-width="2" fill="none"/></svg>
  </div>
  <div class="abs contact-info" style="left:670px;top:54px"><div class="label">Email Us Today</div><div class="value">hello@humasyouroam.com</div></div>
  <div class="abs rule" style="top:96px;left:72px;width:332px"></div>
  <div class="abs rule" style="top:96px;left:548px;width:334px"></div>
  <nav>
    <a class="abs nav" style="left:72px;top:122px">Home</a>
    <a class="abs nav" style="left:112px;top:122px">Brimwell Vacations</a>
    <a class="abs nav" style="left:242px;top:122px">Family Trips</a>
    <a class="abs nav" style="left:328px;top:122px">About Us</a>
    <a class="abs nav" style="left:560px;top:122px">Road Trips from Texas</a>
    <a class="abs nav" style="left:698px;top:122px">Other Destinations</a>
    <a class="abs nav" style="left:834px;top:122px">Contact Us</a>
  </nav>
  <div class="abs rule" style="top:167px;left:204px;width:556px"></div>
  <a class="abs fsocial" style="left:454px;top:154px" aria-label="Share">
    <svg width="11" height="11" viewBox="0 0 24 24"><g fill="#111"><circle cx="18" cy="5" r="3"/><circle cx="6" cy="12" r="3"/><circle cx="18" cy="19" r="3"/></g><path d="M18 5L6 12l12 7" stroke="#111" stroke-width="2" fill="none"/></svg>
  </a>
  <a class="abs fsocial" style="left:484px;top:154px" aria-label="Link">
    <svg width="11" height="11" viewBox="0 0 24 24" fill="none" stroke="#111" stroke-width="2.5" stroke-linecap="round"><path d="M10 14a4 4 0 0 0 6 0l3-3a4 4 0 0 0-6-6l-1 1"/><path d="M14 10a4 4 0 0 0-6 0l-3 3a4 4 0 0 0 6 6l1-1"/></svg>
  </a>
  <p class="abs copyright">Cooyright@2026.All Rights Reserved</p>
</footer>
</body>
</html>
```